Vexa - Booking activities for Kids and Adults.

The app allows booking of Kid's activities for a given date/time.
The app lists activities offered via various clubs (vendors) which a user can book for their kids.
The users can browse various clubs and their offered activities. The users can manage their kid's profiles.
Need a whole new look to the app. The existing app can be checked out at
https://apps.storefrontexample.test/details?id=com.vexakw
https://apps.appmarketexample.test/us/app/vexa-فيكسا/id7302958146?ls=1
Try using the app as Guest.

Target Market(s)

Kuwait

Font styles to use
Serif
Sans Serif

Requirements
Must have
• Home Screens
The home page should have everything from the existing app and a quick area to change between different kid's profile to see activities matching their interests ONLY. In the current version, there's no switch profile and hence we are showing the name tags on the activities.

We are also going to build ecommerce so we need that ecommerce look and feel.
Kindly maintain the image aspect ratio from the current app so the new version doesn't require new images.

Need a complete new innovative designs - Keep the color scheme same.
The designs should be minimalistic and image oriented. The design should be done in XD. The designs should be submitted in both light and dark theme.
Reference to be used - http://plimtor.example

D.M for more info if needed.

```html
<!DOCTYPE html>
<html lang="en">
<head>
<meta charset="utf-8">
<title>Vexa – Schedule</title>
<link rel="stylesheet" href="https://fonts.googleapis.com/css2?family=Poppins:wght@400;500;600;700&display=swap">
<style>
:root{
  --ink:#423f5c;
  --orange:#f5921e;
  --teal:#06dcdc;
  --teal-line:rgba(255,255,255,.35);
  --page:#eef1fa;
  --white:#ffffff;
  --muted:#c9cbd8;
}
*{box-sizing:border-box;margin:0;padding:0}
html,body{width:1200px;height:2591px;overflow:hidden}
body{background:var(--page);font-family:'Poppins',sans-serif;color:var(--ink);position:relative}
.topbar{position:absolute;left:0;top:0;width:1200px;height:326px;background:var(--white);border-radius:0 0 80px 80px;box-shadow:0 10px 30px rgba(66,63,92,.06)}
.menu-dots{position:absolute;left:64px;top:203px;display:flex;gap:9px}
.menu-dots span{width:18px;height:18px;border-radius:50%;background:var(--ink)}
.brand{position:absolute;left:0;width:1200px;top:140px;text-align:center;font-size:88px;font-weight:500;color:var(--orange);line-height:1;letter-spacing:-1px}
.top-icon{position:absolute;top:188px}
.badge{position:absolute;width:26px;height:26px;border-radius:50%;background:var(--orange);color:#fff;font-size:17px;font-weight:600;display:flex;align-items:center;justify-content:center;border:3px solid #fff}
.title{position:absolute;left:64px;top:400px;font-size:82px;font-weight:700;line-height:1.1}
.month{position:absolute;right:88px;top:426px;font-size:42px;font-weight:500;display:flex;align-items:center;gap:16px}
.day{position:absolute;width:140px;margin-left:-70px;text-align:center}
.day .dname{position:absolute;top:585px;width:100%;font-size:38px;font-weight:400}
.day .dnum{position:absolute;top:652px;width:100%;font-size:37px;font-weight:600}
.day.faded{color:var(--muted)}
.day-pill{position:absolute;left:358px;top:553px;width:102px;height:176px;border-radius:51px;background:var(--orange)}
.day-pill .dname{position:absolute;top:32px;width:100%;text-align:center;color:#fff;font-size:38px}
.day-pill .dnum{position:absolute;left:10px;top:94px;width:82px;height:82px;border-radius:50%;background:#fff;display:flex;align-items:center;justify-content:center;font-size:37px;font-weight:600}
.card{position:absolute;left:60px;width:1078px;height:263px;background:var(--white);border-radius:28px;border-left:13px solid var(--orange);box-shadow:0 8px 24px rgba(66,63,92,.05)}
.card.active{background:var(--orange);color:#fff}
.card h2{position:absolute;left:159px;top:58px;font-size:51px;font-weight:700;line-height:1.2;white-space:nowrap}
.card .kids{position:absolute;left:159px;top:135px;font-size:29px;font-weight:500}
.card .times{position:absolute;left:159px;top:182px;display:flex;gap:26px;font-size:30px;font-weight:500}
.card .times span{display:flex;align-items:center;gap:10px}
.card .kebab{position:absolute;left:973px;top:98px;display:flex;flex-direction:column;gap:10px}
.card .kebab i{width:17px;height:17px;border-radius:50%;background:var(--ink)}
.card.active .kebab i{background:#fff}
.sheet{position:absolute;left:3px;top:1751px;width:1194px;height:836px;border-radius:110px;overflow:hidden;color:#fff}
.sheet-art{position:absolute;inset:0;background:linear-gradient(160deg,#0be0e0,#05d8da)}
.action{position:absolute;left:89px;width:1046px;display:flex;align-items:center;gap:26px;font-size:48px;font-weight:700;padding-left:262px}
.action svg{width:70px;height:70px;margin-left:-96px;margin-right:0}
.rule{position:absolute;left:89px;width:1046px;height:2px;background:var(--teal-line)}
.cancel{position:absolute;left:0;width:1194px;top:712px;text-align:center;font-size:57px;font-weight:600}
</style>
</head>
<body>
<header class="topbar">
  <div class="menu-dots"><span></span><span></span><span></span></div>
  <div class="brand">Vexa</div>
  <svg class="top-icon" style="left:972px" width="60" height="66" viewBox="0 0 60 66" fill="none" stroke="#423f5c" stroke-width="4" stroke-linejoin="round"><path d="M10 48V30a20 20 0 0 1 40 0v18l6 6H4z"/><path d="M23 58a7 7 0 0 0 14 0"/></svg>
  <div class="badge" style="left:1008px;top:188px">0</div>
  <svg class="top-icon" style="left:1052px;top:192px" width="76" height="62" viewBox="0 0 76 62" fill="none" stroke="#423f5c" stroke-width="4" stroke-linejoin="round"><path d="M22 22L38 4l16 18"/><path d="M4 22h68v10H4z"/><path d="M8 32l6 26h48l6-26"/><path d="M26 40v10M38 40v10M50 40v10"/></svg>
  <div class="badge" style="left:1112px;top:188px">0</div>
</header>

<h1 class="title">Schedule</h1>
<div class="month">June 2019
  <svg width="24" height="16" viewBox="0 0 24 16" fill="none" stroke="#423f5c" stroke-width="3.5"><path d="M4 4l8 8 8-8"/></svg>
</div>

<nav class="days">
  <div class="day" style="left:105px"><div class="dname">Wed</div><div class="dnum">20</div></div>
  <div class="day" style="left:263px"><div class="dname">Thu</div><div class="dnum">21</div></div>
  <div class="day-pill"><div class="dname">Fri</div><div class="dnum">22</div></div>
  <div class="day" style="left:555px"><div class="dname">Sat</div><div class="dnum">23</div></div>
  <div class="day" style="left:721px"><div class="dname">Sun</div><div class="dnum">24</div></div>
  <div class="day" style="left:871px"><div class="dname">Mon</div><div class="dnum">25</div></div>
  <div class="day" style="left:1036px"><div class="dname">Tue</div><div class="dnum">26</div></div>
  <div class="day faded" style="left:1210px"><div class="dname">Wed</div><div class="dnum">27</div></div>
</nav>

<section class="activities">
  <article class="card" style="top:793px">
    <h2>Reading for Tots</h2>
    <div class="kids">Maha, Tariq</div>
    <div class="times">
      <span><svg width="26" height="26" viewBox="0 0 26 26" fill="none" stroke="#06dcdc" stroke-width="2.5"><circle cx="13" cy="13" r="11"/><path d="M13 6v7l4 3"/></svg>10:00 am</span>
      <span><svg width="26" height="26" viewBox="0 0 26 26" fill="none" stroke="#06dcdc" stroke-width="2.5"><circle cx="13" cy="13" r="11"/><path d="M13 6v7l4 3"/></svg>1:00 am</span>
    </div>
    <div class="kebab"><i></i><i></i><i></i></div>
  </article>
  <article class="card active" style="top:1079px">
    <h2>Swimming for Begginers</h2>
    <div class="kids">Maha, Tariq</div>
    <div class="times">
      <span><svg width="26" height="26" viewBox="0 0 26 26" fill="none" stroke="#ffffff" stroke-width="2.5"><circle cx="13" cy="13" r="11"/><path d="M13 6v7l4 3"/></svg>10:00 am</span>
      <span><svg width="26" height="26" viewBox="0 0 26 26" fill="none" stroke="#ffffff" stroke-width="2.5"><circle cx="13" cy="13" r="11"/><path d="M13 6v7l4 3"/></svg>1:00 am</span>
    </div>
    <div class="kebab"><i></i><i></i><i></i></div>
  </article>
  <article class="card" style="top:1369px">
    <h2>Swiming Level 2</h2>
    <div class="kids">Maha, Tariq</div>
    <div class="times">
      <span><svg width="26" height="26" viewBox="0 0 26 26" fill="none" stroke="#06dcdc" stroke-width="2.5"><circle cx="13" cy="13" r="11"/><path d="M13 6v7l4 3"/></svg>10:00 am</span>
      <span><svg width="26" height="26" viewBox="0 0 26 26" fill="none" stroke="#06dcdc" stroke-width="2.5"><circle cx="13" cy="13" r="11"/><path d="M13 6v7l4 3"/></svg>1:00 am</span>
    </div>
    <div class="kebab"><i></i><i></i><i></i></div>
  </article>
</section>

<section class="sheet">
  <div class="sheet-art" role="img" aria-label="Faint doodle pattern of children's toys and play items on turquoise"></div>
  <div class="action" style="top:81px">
    <svg viewBox="0 0 70 70" fill="#fff"><path d="M40 14l24 20-24 20V42C24 42 14 48 6 60c2-20 12-34 34-36z"/></svg>Share</div>
  <div class="rule" style="top:186px"></div>
  <div class="action" style="top:234px">
    <svg viewBox="0 0 70 70" fill="none" stroke="#fff" stroke-width="5" stroke-linecap="round"><path d="M18 10l10 12-6 6c4 8 10 14 18 18l6-6 12 10-6 8C30 58 12 40 10 18z" fill="#fff"/><path d="M40 14a16 16 0 0 1 16 16M40 4a26 26 0 0 1 26 26"/></svg>Call</div>
  <div class="rule" style="top:342px"></div>
  <div class="action" style="top:386px">
    <svg viewBox="0 0 70 70" fill="none" stroke="#fff" stroke-width="5"><rect x="12" y="14" width="46" height="44" rx="3"/><path d="M12 26h46M22 8v10M48 8v10"/><path d="M22 36h6M32 36h6M42 36h6M22 46h6M32 46h6M42 46h6" stroke-width="5"/></svg>Add to Calendar</div>
  <div class="rule" style="top:493px"></div>
  <div class="action" style="top:539px">
    <svg viewBox="0 0 70 70"><path d="M35 4l31 31-31 31L4 35z" fill="#fff"/><path d="M28 46V34h14" fill="none" stroke="#06dcdc" stroke-width="5"/><path d="M38 27l8 7-8 7z" fill="#06dcdc"/></svg>Directions</div>
  <div class="rule" style="top:671px"></div>
  <div class="cancel">Cancel</div>
</section>
</body>
</html>
```